Health Care Company with Logo Needs Business Cards designed

We are a luxury behavioral health company looking for business cards design we already have a logo and are looking for someone to design a sophisticated luxurious looking business card. Please note that Card design should be captivating just like the logo and also encompass the logo color

Industry/Entity Type

Healthcare

Contact Information for Business Card

Logo,company name, tagline, my name and title, contact details, and physical address

```html
<!DOCTYPE html>
<html lang="en">
<head>
<meta charset="utf-8">
<title>Orin Behavioral Health – Business Cards</title>
<link href="https://fonts.googleapis.com/css2?family=Roboto+Condensed:wght@400;700&family=Roboto:ital,wght@0,400;1,400&display=swap" rel="stylesheet">
<style>
  :root {
    --backdrop: #2a2a2a;
    --card: #232324;
    --front-ink: #8e8e90;
    --ink-light: #e4e4e4;
    --muted: #d2d2d2;
    --purple: #6e3a8f;
    --blue: #1b90cf;
    --orange: #e38a14;
    --green: #8ab42a;
  }
  * { margin: 0; padding: 0; box-sizing: border-box; }
  html, body { width: 1200px; height: 1138px; overflow: hidden; }
  body {
    background: var(--backdrop);
    position: relative;
    font-family: "Roboto", Arial, sans-serif;
  }
  .card {
    position: absolute;
    background: var(--card);
    border-radius: 16px;
    overflow: hidden;
  }
  /* Front */
  .card-front { left: 274px; top: 186px; width: 624px; height: 376px; }
  .front-mark {
    position: absolute; left: 237px; top: 56px;
    width: 150px; height: 150px; background: var(--front-ink);
  }
  .front-name {
    position: absolute; left: 0; right: 0; top: 248px; text-align: center;
    font-family: "Roboto Condensed", Arial, sans-serif;
    font-weight: 700; font-size: 40px; line-height: 1; color: var(--front-ink);
  }
  .front-tagline {
    position: absolute; left: 0; right: 0; top: 342px; text-align: center;
    font-family: "Roboto Condensed", Arial, sans-serif; font-weight: 700;
    font-size: 12.5px; letter-spacing: 2.6px; color: var(--muted);
  }
  /* Back */
  .card-back { left: 276px; top: 608px; width: 618px; height: 374px; }
  .accent-block {
    position: absolute; left: 60px; top: 90px; width: 180px; height: 180px;
    background: var(--orange);
  }
  .back-info {
    position: absolute; right: 25px; top: 38px; text-align: right;
  }
  .company {
    font-family: "Roboto Condensed", Arial, sans-serif; font-weight: 700;
    font-size: 34px; line-height: 1; color: var(--purple);
  }
  .tagline {
    margin-top: 6px;
    font-family: "Roboto Condensed", Arial, sans-serif; font-weight: 700;
    font-size: 11.5px; letter-spacing: 2.4px; color: var(--blue);
  }
  .person {
    margin-top: 52px;
    font-family: "Roboto Condensed", Arial, sans-serif; font-weight: 700;
    font-size: 24px; line-height: 1; color: var(--purple);
  }
  .role {
    margin-top: 8px; font-style: italic; font-size: 15px; color: var(--ink-light);
  }
  .address {
    margin-top: 24px; font-size: 15px; line-height: 22px; color: var(--ink-light);
  }
  .contacts { margin-top: 10px; list-style: none; }
  .contacts li {
    display: flex; justify-content: flex-end; align-items: center; gap: 13px;
    font-size: 15px; line-height: 22px; color: var(--ink-light);
  }
  .contacts svg { width: 14px; height: 14px; }
</style>
</head>
<body>
  <section class="card card-front" aria-label="Card front">
    <span class="front-mark"></span>
    <p class="front-name">Orin Behavioral Health</p>
    <p class="front-tagline">DEDICATED TO HOPE, HEALING AND RECOVERY</p>
  </section>

  <section class="card card-back" aria-label="Card back">
    <div class="accent-block"></div>
    <div class="back-info">
      <h1 class="company">Orin Behavioral Health</h1>
      <p class="tagline">DEDICATED TO HOPE, HEALING AND RECOVERY</p>
      <h2 class="person">DANIEL REYES</h2>
      <p class="role">Managing Director</p>
      <p class="address">123, Anywhere ST, Any City,<br>Any Town, US 123456</p>
      <ul class="contacts">
        <li>000-111-0000
          <svg viewBox="0 0 14 14" aria-hidden="true"><path d="M1 5c0-2 2-3 6-3s6 1 6 3v1h-3V4.5H4V6H1z M3 7h8l1.5 5h-11z" fill="var(--purple)"/></svg>
        </li>
        <li>daniel@orinbehavioral.com
          <svg viewBox="0 0 14 14" aria-hidden="true"><rect x="0.5" y="2.5" width="13" height="9" fill="var(--purple)"/><path d="M0.5 2.5l6.5 5 6.5-5" fill="none" stroke="#fff" stroke-width="1"/></svg>
        </li>
        <li>www.orinbehavioral.com
          <svg viewBox="0 0 14 14" aria-hidden="true"><circle cx="7" cy="7" r="6" fill="none" stroke="var(--purple)" stroke-width="1.3"/><ellipse cx="7" cy="7" rx="2.6" ry="6" fill="none" stroke="var(--blue)" stroke-width="1"/><path d="M1 7h12" stroke="var(--blue)" stroke-width="1"/></svg>
        </li>
      </ul>
    </div>
  </section>
</body>
</html>
```